Business Card Design

I already have a company logo for my company. I have a logo for the manufacturer we represent. I want a professional business card design.

```html
<!DOCTYPE html>
<html lang="en">
<head>
<meta charset="utf-8">
<title>Signal Point LLC – Business Card</title>
<link rel="stylesheet" href="https://fonts.googleapis.com/css2?family=Open+Sans:wght@400;600;800&display=swap">
<style>
  :root {
    --page: #2e2e2e;
    --card: #151515;
    --red: #e3212b;
    --yellow: #e0a928;
    --white: #f2f2f2;
    --muted: #e6e6e6;
  }
  * { box-sizing: border-box; margin: 0; padding: 0; }
  html, body { width: 1200px; height: 780px; overflow: hidden; }
  body {
    background: var(--page);
    font-family: "Open Sans", Arial, sans-serif;
    position: relative;
  }
  .card {
    position: absolute;
    width: 540px;
    height: 309px;
    background: var(--card);
    border-radius: 22px;
    overflow: hidden;
    box-shadow: 0 10px 28px rgba(0,0,0,0.45);
  }
  .card--front { left: 40px; top: 236px; }
  .card--back  { left: 620px; top: 236px; }

  .card__wave { position: absolute; inset: 0; width: 100%; height: 100%; }

  .brand {
    position: absolute;
    display: flex;
    align-items: center;
    gap: 10px;
    color: var(--white);
    font-weight: 800;
    text-transform: uppercase;
    letter-spacing: 0.02em;
    line-height: 1.05;
    white-space: nowrap;
  }
  .brand__name span { display: block; }
  .brand__mark { background: var(--red); flex: none; }
  .card--front .brand { left: 56px; top: 62px; font-size: 24px; }
  .card--front .brand__mark { width: 20px; height: 20px; }
  .card--back .brand { left: 50%; top: 50%; transform: translate(-50%, -50%); font-size: 38px; gap: 14px; }
  .card--back .brand__mark { width: 32px; height: 32px; }

  .divider {
    position: absolute;
    left: 328px; top: 62px;
    width: 1.5px; height: 150px;
    background: var(--red);
  }

  .contact { position: absolute; left: 344px; top: 62px; color: var(--muted); }
  .contact__name {
    color: var(--red);
    font-weight: 600;
    font-size: 19px;
    text-transform: uppercase;
    letter-spacing: 0.01em;
    line-height: 1.1;
  }
  .contact__role { font-size: 12.5px; margin-bottom: 10px; }
  .contact__list { list-style: none; font-size: 12.5px; line-height: 1.55; }
  .contact__list li { display: flex; align-items: center; gap: 6px; }
  .contact__icon { width: 10px; height: 10px; flex: none; fill: var(--red); }
  .contact__address { font-size: 12.5px; line-height: 1.45; margin-top: 6px; }
</style>
</head>
<body>

  <section class="card card--front" aria-label="Business card front">
    <svg class="card__wave" viewBox="0 0 540 309" preserveAspectRatio="none" aria-hidden="true">
      <path d="M110,215 C200,265 360,262 540,262 L540,309 L0,309 Z" fill="var(--red)"/>
      <path d="M0,135 C60,130 100,190 140,232 C185,280 250,300 330,309 L0,309 Z"
            fill="var(--yellow)" stroke="#0a0a0a" stroke-width="5"/>
    </svg>

    <div class="brand"><span class="brand__mark"></span><span class="brand__name"><span>Signal Point</span><span>LLC</span></span></div>

    <div class="divider"></div>

    <div class="contact">
      <p class="contact__name">Daniel Reyes</p>
      <p class="contact__role">Managing Director</p>
      <ul class="contact__list">
        <li>
          <svg class="contact__icon" viewBox="0 0 10 10"><path d="M2 0.5 L3.6 2.6 L2.8 3.6 C3.4 4.9 4.6 6.2 6.2 7 L7.2 6.2 L9.5 7.8 L8.4 9.5 C4.5 9.2 0.8 5.5 0.5 1.6 Z"/></svg>
          123 456 789
        </li>
        <li>
          <svg class="contact__icon" viewBox="0 0 10 10"><path d="M0 2 H10 V8.5 H0 Z M0.6 2.5 L5 5.6 L9.4 2.5" stroke="#151515" stroke-width="0.7"/></svg>
          info@yourmail.com
        </li>
        <li>
          <svg class="contact__icon" viewBox="0 0 10 10"><circle cx="5" cy="5" r="4.6"/><path d="M0.5 5 H9.5 M5 0.4 C3 3 3 7 5 9.6 M5 0.4 C7 3 7 7 5 9.6" stroke="#151515" stroke-width="0.7" fill="none"/></svg>
          www.yourwebsite.com
        </li>
      </ul>
      <p class="contact__address">Your address, City<br>State, Zip 1234</p>
    </div>
  </section>

  <section class="card card--back" aria-label="Business card back">
    <div class="brand"><span class="brand__mark"></span><span class="brand__name"><span>Signal Point</span><span>LLC</span></span></div>
  </section>

</body>
</html>
```